Falkrin homes and renovations business card design.

Would like some new card designs utilizing my new logo that look professional. I am open to different colors on the logo or utilize the same ones we have. I like the original concept but would like to see some fresh ideas and build on what we have already done.

Target Market(s)

Custom home building industry, Real estate sales, Renovation projects.

Industry/Entity Type

Home Builder

Contact Information for Business Card

Falkrin Homes and Renovations
2871 96th Avenue
Frank, Alberta
T2R3W8
Home : 403- 718-4063 Cell: 403- 294-5170

My info is : Dax Falkrin, President and CEO
email: falkrinhomes@maildrop-example.net
Website: falkrinhomes-example.com
websit

Requirements
Must have
• Must Use my new logo design. I am open to different colors on the logo or utilize the same ones in the existing design. I can upload the original logo design if needed.

```html
<!DOCTYPE html>
<html lang="en">
<head>
<meta charset="utf-8">
<title>Falkrin Homes and Renovations – Business Card</title>
<link rel="stylesheet" href="https://fonts.googleapis.com/css2?family=Roboto+Condensed:wght@400;700&display=swap">
<style>
  :root {
    --sheet: #ffffff;
    --frame: #1a1a1a;
    --card: #000000;
    --gold: #b8862b;
    --grey: #7a7a7a;
    --white: #ffffff;
    --red: #e8323a;
    --red-deep: #7a0d12;
    --curl-light: #f2f2f2;
    --curl-dark: #9a9a9a;
  }
  * { margin: 0; padding: 0; box-sizing: border-box; }
  html, body { width: 1200px; height: 1001px; overflow: hidden; background: var(--sheet); }
  body { font-family: "Roboto Condensed", "Arial Narrow", sans-serif; position: relative; }

  .sheet-frame {
    position: absolute; left: 1px; top: 1px; width: 1199px; height: 999px;
    border: 1.5px solid var(--frame);
  }
  .card {
    position: absolute; width: 814px; height: 461px;
    background: var(--card); border: 1.5px solid var(--frame); overflow: hidden;
  }
  .card--front { left: 81px; top: 38px; }
  .card--back { left: 311px; top: 505px; }

  .page-curl { position: absolute; left: 0; top: 0; width: 814px; height: 461px; }

  .brand-name {
    position: absolute; font-weight: 700; font-size: 30px; line-height: 36px;
    letter-spacing: 1px; text-transform: uppercase;
  }
  .card--front .brand-name { left: 249px; top: 70px; width: 240px; color: var(--gold); }
  .card--back .brand-name { left: 42px; top: 62px; width: 240px; color: var(--grey); }

  .holder { position: absolute; left: 249px; top: 280px; color: var(--gold); }
  .holder__name { font-weight: 700; font-size: 29px; line-height: 40px; }
  .holder__title { font-weight: 400; font-size: 28px; line-height: 42px; }

  .services {
    position: absolute; left: 249px; top: 369px; color: var(--white);
    font-size: 24px; line-height: 35px;
  }

  .company {
    position: absolute; left: 355px; top: 84px; color: var(--white);
    font-weight: 700; font-size: 27px; line-height: 38px; letter-spacing: 0.5px;
  }
  .contact {
    position: absolute; left: 355px; top: 312px; color: var(--white);
    font-size: 23px; line-height: 33px; list-style: none;
  }
</style>
</head>
<body>
  <div class="sheet-frame"></div>

  <section class="card card--front">
    <svg class="page-curl" viewBox="0 0 814 461" aria-hidden="true">
      <defs>
        <linearGradient id="frontRed" x1="0" y1="1" x2="1" y2="0">
          <stop offset="0" stop-color="var(--red)"/>
          <stop offset="0.6" stop-color="var(--red)"/>
          <stop offset="1" stop-color="var(--red-deep)"/>
        </linearGradient>
        <linearGradient id="frontCurl" x1="0" y1="0" x2="1" y2="1">
          <stop offset="0" stop-color="var(--curl-light)"/>
          <stop offset="0.55" stop-color="#d6d6d6"/>
          <stop offset="1" stop-color="var(--curl-dark)"/>
        </linearGradient>
      </defs>
      <path d="M0 269 L0 461 L242 461 C150 440 60 380 2 269 Z" fill="url(#frontRed)"/>
      <path d="M2 269 C60 280 150 285 178 287 L180 360 C185 400 210 432 242 461 C150 440 60 380 2 269 Z" fill="url(#frontCurl)"/>
    </svg>
    <div class="brand-name">Falkrin Homes and Renovations</div>
    <div class="holder">
      <p class="holder__name">Dax Falkrin</p>
      <p class="holder__title">President and CEO</p>
    </div>
    <p class="services">Custom Home Building Industry,<br>Real Estate Sales, Renovation Projects</p>
  </section>

  <section class="card card--back">
    <svg class="page-curl" viewBox="0 0 814 461" aria-hidden="true">
      <defs>
        <linearGradient id="backRed" x1="0" y1="1" x2="1" y2="0">
          <stop offset="0" stop-color="var(--red)"/>
          <stop offset="0.6" stop-color="var(--red)"/>
          <stop offset="1" stop-color="var(--red-deep)"/>
        </linearGradient>
        <linearGradient id="backCurl" x1="0" y1="0" x2="1" y2="1">
          <stop offset="0" stop-color="var(--curl-light)"/>
          <stop offset="0.55" stop-color="#d6d6d6"/>
          <stop offset="1" stop-color="var(--curl-dark)"/>
        </linearGradient>
      </defs>
      <path d="M0 269 L0 461 L242 461 C150 440 60 380 2 269 Z" fill="url(#backRed)"/>
      <path d="M2 269 C60 280 150 285 176 287 L178 360 C185 400 210 432 242 461 C150 440 60 380 2 269 Z" fill="url(#backCurl)"/>
    </svg>
    <div class="brand-name">Falkrin Homes and Renovations</div>
    <h1 class="company">FALKRIN<br>HOMES AND RENOVATIONS</h1>
    <ul class="contact">
      <li>2871 96th Avenue Frank, Alberta, T2R3W8</li>
      <li>Email: falkrinhomes@maildrop-example.net</li>
      <li>Website: falkrinhomes-example.com</li>
      <li>Home : 403- 718-4063 Cell: 403- 294-5170</li>
    </ul>
  </section>
</body>
</html>
```